Redesign of business card for Cedar Ridge Mechanical

We are looking for a new design for our business cards for Cedar Ridge Mechanical. We are a plumbing & HVAC construction company, operating on the West Coast of Canada and USA. Logo attached.
Industry/Entity Type
Construction - Plumbing & HVAC
Contact Information for Business Card
Name, address, phone numbers, email, website address
Look and feel
Each slider illustrates characteristics of the customer's brand and the style your logo design should communicate.

```html
<!DOCTYPE html>
<html lang="en">
<head>
<meta charset="UTF-8">
<title>Cedar Ridge Mechanical – Business Card</title>
<link href="https://fonts.googleapis.com/css2?family=Oswald:wght@600&family=Montserrat:wght@400;700&display=swap" rel="stylesheet">
<style>
  :root {
    --backdrop: #3b3b3b;
    --card: #ffffff;
    --ink: #111111;
    --ink-soft: #2a2a2a;
  }
  * { box-sizing: border-box; margin: 0; padding: 0; }
  html, body {
    width: 1200px; height: 689px; overflow: hidden;
    background: var(--backdrop);
  }
  .canvas {
    position: relative; width: 1200px; height: 689px;
    display: flex; align-items: center; justify-content: center; gap: 40px;
  }
  .card {
    position: relative; width: 540px; height: 309px;
    background: var(--card); color: var(--ink);
  }
  /* Front side */
  .card-front { display: flex; align-items: center; justify-content: center; }
  .brand { display: flex; align-items: center; gap: 14px; }
  .brand-square { width: 34px; height: 34px; background: var(--ink); flex: none; }
  .brand-name {
    font-family: "Oswald", sans-serif; font-weight: 600;
    font-size: 34px; letter-spacing: 1.5px; text-transform: uppercase;
  }
  /* Back side */
  .brand-small { position: absolute; top: 30px; right: 34px; gap: 7px; }
  .brand-small .brand-square { width: 12px; height: 12px; }
  .brand-small .brand-name { font-size: 13px; letter-spacing: 0.8px; }
  .details {
    position: absolute; top: 108px; left: 0; right: 0;
    display: flex; align-items: center; justify-content: center; gap: 22px;
  }
  .person { text-align: right; font-family: "Montserrat", sans-serif; }
  .person-name { font-weight: 700; font-size: 22px; letter-spacing: 0.5px; }
  .person-role { font-weight: 400; font-size: 13px; color: var(--ink-soft); margin-top: 2px; }
  .divider { width: 1.5px; height: 70px; background: var(--ink); }
  .contacts { list-style: none; font-family: "Montserrat", sans-serif; font-size: 13px; color: var(--ink-soft); }
  .contacts li { display: flex; align-items: center; gap: 8px; line-height: 22px; }
  .contacts svg { width: 12px; height: 12px; flex: none; }
  .address {
    position: absolute; bottom: 30px; right: 34px;
    font-family: "Montserrat", sans-serif; font-size: 13px; color: var(--ink-soft);
  }
</style>
</head>
<body>
<main class="canvas">
  <section class="card card-front" aria-label="Business card front">
    <div class="brand">
      <span class="brand-square"></span>
      <span class="brand-name">Cedar Ridge Mechanical</span>
    </div>
  </section>

  <section class="card card-back" aria-label="Business card back">
    <div class="brand brand-small">
      <span class="brand-square"></span>
      <span class="brand-name">Cedar Ridge Mechanical</span>
    </div>

    <div class="details">
      <div class="person">
        <p class="person-name">DANIEL HAYES</p>
        <p class="person-role">Managing Director</p>
      </div>
      <span class="divider"></span>
      <ul class="contacts">
        <li>
          <svg viewBox="0 0 12 12" aria-hidden="true"><path d="M2 1h2.5l1 3-1.5 1a7 7 0 0 0 3 3l1-1.5 3 1V11c-5 .5-9.5-4-9-10z" fill="#111"/></svg>
          604 555 0187
        </li>
        <li>
          <svg viewBox="0 0 12 12" aria-hidden="true"><rect x="0.5" y="2" width="11" height="8" fill="none" stroke="#111"/><path d="M0.5 2l5.5 4.5L11.5 2" fill="none" stroke="#111"/></svg>
          info@cedarridgemech.com
        </li>
        <li>
          <svg viewBox="0 0 12 12" aria-hidden="true"><circle cx="6" cy="6" r="5.3" fill="none" stroke="#111"/><ellipse cx="6" cy="6" rx="2.3" ry="5.3" fill="none" stroke="#111"/><path d="M0.7 6h10.6" stroke="#111"/></svg>
          www.cedarridgemech.com
        </li>
      </ul>
    </div>

    <p class="address">218 Harbour Road, Vancouver BC, V6B 1A1</p>
  </section>
</main>
</body>
</html>
```